Etiketten-Design für Kaffeetüten
Zielgruppe
Wir stellen eine nachhaltige alternative zu herkömmlichem Bohnenkaffee her.
Regional, nachhaltig und koffeinfrei.
Hierzu verwenden wir Süßlupinen die wir von einem Partnerbauern aus Niedersachsen beziehen. Diese Lupinen werden wie herkömmlicher Kaffee in einem Trommelröster geröstet und anschließend gemahlen.
Unser Lupinenkaffee kann wie herkömmlicher Kaffee im Filter in der Frenchpress oder in einem Espressokocher zubereitet werden.
Wir bieten unseren Kunden zwei verschiedene Sorten an, eine 'Mild' und eine 'Klassisch'.
Die Zielgruppe sind ernährungsbewusste Menschen die gezielt eine alternative zu herkömmlichen Bohnenkaffee suchen. (Koffeinfreier Kaffee, Getreidekaffee)
Aufgabenstellung
Wir möchten ein modernes Design des Etiketts, das den Stil des Logos widerspiegelt. Die beiden Sorten 'Mild' und 'Klassisch' sollten gut von einander zu unterscheiden sein.
Es gibt ein Etikett für die Vorderseite, hier soll die Produktbezeichnung 'Lupinenkaffee' sowie die Mengenangabe '500g' stehen.
Ggf. 3 Icons für mögliche Brühmethoden (Filter, Frenchpress, Espressokocher)
Auf dem Etikett der Rückseite müssen zum einen die Zutaten, die Zubereitung sowie die Nährwertangaben (in TabellenForm) angegeben werden. Sowie ein EAN Code die Herstellerangaben und die Adresse der Homepage.
TREVO KAFFEE – Deine nachhaltige Kaffeealternative
Zutaten: weiße Süßlupinen, geröstet
Zubereitung: Du kannst Deinen Lupinenkaffee mit der French Press, dem klassischen Filter oder dem Espressokocher zubereiten. Für den optimalen Geschmack empfehlen wir 8g Kaffeepulver für 100ml.
Hersteller:
TREVO GmbH
Henrietta-Lenz-Weg 47
40477 Düsseldorf
www.TREVOKAFFEE.de
 Nährwertangaben für 100 ml Kaffee
Energie 12kj - 5 kcal
Fett <0,1g
Davon gesättigt <0,1g
Kohlenhydrate <1,0g
Davon Zucker <0,05g
Eiweiß <1,0g
Salz <0,05g
Die Kaffeetüte, auf die das Etikett geklebt wird, ist in einer braunen Kartonfarbe.
Das Etikett für die Kaffeetüten hat die Maße 7x11.
Das Logo hat die Schriftart 'Cera'. Die verwendete Schriftart sollte möglichst gleich sein, oder gut damit harmonieren.

```html
<!DOCTYPE html>
<html lang="de">
<head>
<meta charset="utf-8">
<title>Lupinenkaffee Etiketten – Classic und Mild</title>
<link rel="stylesheet" href="https://fonts.googleapis.com/css2?family=Ubuntu:wght@300;400;500;700&display=swap">
<style>
  :root {
    --backdrop: #e8e9ea;
    --label-dark: #404040;
    --classic: #d1007f;
    --mild: #76996a;
    --ink-light: #ffffff;
    --label-w: 430px;
    --label-h: 702px;
  }
  * { box-sizing: border-box; margin: 0; padding: 0; }
  html, body {
    width: 1200px;
    height: 898px;
    overflow: hidden;
    background: var(--backdrop);
    font-family: "Ubuntu", sans-serif;
  }
  .canvas {
    position: relative;
    width: 1200px;
    height: 898px;
  }
  .label {
    position: absolute;
    top: 98px;
    width: var(--label-w);
    height: var(--label-h);
    background: var(--label-dark);
    color: var(--ink-light);
    overflow: hidden;
  }
  .label--classic { left: 85px; --variant: var(--classic); }
  .label--mild { left: 685px; --variant: var(--mild); }

  .variant-band {
    position: absolute;
    left: 0; top: 0;
    width: 109px;
    height: 100%;
    background: var(--variant);
  }
  .product-word {
    position: absolute;
    left: 109px; top: 0;
    width: 82px;
    height: 100%;
  }
  .product-word text {
    fill: var(--variant);
    font-family: "Ubuntu", sans-serif;
    font-weight: 300;
  }

  .brand {
    position: absolute;
    left: 0; top: 255px;
    width: 109px;
    text-align: center;
  }
  .brand-circle {
    display: block;
    width: 86px;
    height: 86px;
    margin: 0 auto;
    border: 1.5px solid var(--ink-light);
    border-radius: 50%;
  }
  .brand-name {
    display: block;
    margin-top: 12px;
    font-size: 11px;
    font-weight: 400;
    letter-spacing: 1.5px;
    color: var(--ink-light);
  }

  .content {
    position: absolute;
    left: 212px; top: 258px;
    right: 20px;
  }
  .variant-name {
    font-size: 42px;
    font-weight: 500;
    line-height: 1;
    letter-spacing: 0.5px;
  }
  .claim {
    margin-top: 10px;
    font-size: 23px;
    font-weight: 300;
    line-height: 32px;
  }
  .features {
    list-style: none;
    margin-top: 38px;
    font-size: 23px;
    font-weight: 300;
    line-height: 36px;
  }
  .brew-methods {
    display: flex;
    align-items: center;
    gap: 8px;
    margin-top: 30px;
  }
  .brew-methods svg {
    stroke: var(--ink-light);
    fill: none;
    stroke-width: 2;
    stroke-linejoin: round;
    stroke-linecap: round;
  }
</style>
</head>
<body>
<main class="canvas">

  <section class="label label--classic" aria-label="Etikett Lupinenkaffee Classic">
    <div class="variant-band"></div>
    <svg class="product-word" viewBox="0 0 82 702" aria-hidden="true">
      <text x="0" y="0" font-size="118" textLength="702" lengthAdjust="spacingAndGlyphs" transform="translate(82 702) rotate(-90)">LUPPINENKAFFE</text>
    </svg>
    <div class="brand">
      <span class="brand-circle"></span>
      <span class="brand-name">TREVO KAFFEE</span>
    </div>
    <div class="content">
      <h2 class="variant-name">CLASSIC</h2>
      <p class="claim">Deine nachhaltige<br>Kaffeealternative</p>
      <ul class="features">
        <li>Koffeinfrei</li>
        <li>Vegan</li>
        <li>Glutenfrei</li>
      </ul>
      <div class="brew-methods">
        <svg class="icon-moka" width="44" height="50" viewBox="0 0 44 50" aria-label="Espressokocher" role="img">
          <path d="M16 4h12l-1 5H17z"/><path d="M13 9h18l-3 15H16z"/><path d="M16 24h12l4 22H12z"/>
          <path d="M31 12c6 0 7 8 1 10"/><path d="M13 12l-6 3"/>
        </svg>
        <svg class="icon-filter" width="72" height="50" viewBox="0 0 72 50" aria-label="Filter" role="img">
          <path d="M3 14 Q36 0 69 14 L46 44 H26 Z"/><path d="M14 12 L32 44"/>
        </svg>
        <svg class="icon-press" width="44" height="50" viewBox="0 0 44 50" aria-label="French Press" role="img">
          <path d="M20 3v8"/><path d="M16 3h8"/><path d="M10 11h20"/><path d="M11 14h18v32H11z"/>
          <path d="M11 22h18"/><path d="M29 18h6a3 3 0 0 1 3 3v16a3 3 0 0 1-3 3h-6"/><path d="M9 46h22"/>
        </svg>
      </div>
    </div>
  </section>

  <section class="label label--mild" aria-label="Etikett Lupinenkaffee Mild">
    <div class="variant-band"></div>
    <svg class="product-word" viewBox="0 0 82 702" aria-hidden="true">
      <text x="0" y="0" font-size="118" textLength="702" lengthAdjust="spacingAndGlyphs" transform="translate(82 702) rotate(-90)">LUPPINENKAFFE</text>
    </svg>
    <div class="brand">
      <span class="brand-circle"></span>
      <span class="brand-name">TREVO KAFFEE</span>
    </div>
    <div class="content">
      <h2 class="variant-name">MILD</h2>
      <p class="claim">Deine nachhaltige<br>Kaffeealternative</p>
      <ul class="features">
        <li>Koffeinfrei</li>
        <li>Vegan</li>
        <li>Glutenfrei</li>
      </ul>
      <div class="brew-methods">
        <svg class="icon-moka" width="44" height="50" viewBox="0 0 44 50" aria-label="Espressokocher" role="img">
          <path d="M16 4h12l-1 5H17z"/><path d="M13 9h18l-3 15H16z"/><path d="M16 24h12l4 22H12z"/>
          <path d="M31 12c6 0 7 8 1 10"/><path d="M13 12l-6 3"/>
        </svg>
        <svg class="icon-filter" width="72" height="50" viewBox="0 0 72 50" aria-label="Filter" role="img">
          <path d="M3 14 Q36 0 69 14 L46 44 H26 Z"/><path d="M14 12 L32 44"/>
        </svg>
        <svg class="icon-press" width="44" height="50" viewBox="0 0 44 50" aria-label="French Press" role="img">
          <path d="M20 3v8"/><path d="M16 3h8"/><path d="M10 11h20"/><path d="M11 14h18v32H11z"/>
          <path d="M11 22h18"/><path d="M29 18h6a3 3 0 0 1 3 3v16a3 3 0 0 1-3 3h-6"/><path d="M9 46h22"/>
        </svg>
      </div>
    </div>
  </section>

</main>
</body>
</html>
```